ReelBloom business card

We are a performing arts company providing training (to both kids and adults) as well as performers for events. We hope to bring joy and confidence on stage to the people we train, as well as joy to the audience when our artistes perform. Designs should convey the joy, confidence and vibrancy on stage. Design business card using the attached logo. Card to include name, mobile tel, email address, company address, and website. Double sided. To also include the following list of what the company does:
• Training & Enrichment
• Private & Corporate Entertainment
- Music composition & production

Industry/Entity Type

Training

Contact Information for Business Card

Card to include name, mobile tel, email address, company address, and website. Double sided. To also include the following list of what the company does:
• Training & Enrichment

Requirements
Nice to have
• Card need not be the traditional rectangular in shape but not too outrageous.

```html
<!DOCTYPE html>
<html lang="en">
<head>
<meta charset="utf-8">
<title>ReelBloom Business Card</title>
<link href="https://fonts.googleapis.com/css2?family=Open+Sans:wght@300;400;600;700&display=swap" rel="stylesheet">
<style>
  :root {
    --page-bg: #e6e4e0;
    --card-white: #ffffff;
    --card-shade: #f1f1f1;
    --navy: #15266b;
    --navy-deep: #0d1a52;
    --lime: #8cc63f;
    --ink: #333333;
    --brand: #6a2c91;
    --on-navy: #ffffff;
  }
  * { margin: 0; padding: 0; box-sizing: border-box; }
  html, body {
    width: 1200px; height: 885px; overflow: hidden;
    background: var(--page-bg);
    font-family: "Open Sans", Arial, sans-serif;
  }
  .canvas {
    position: relative; width: 1200px; height: 885px;
    display: flex; align-items: center; justify-content: center; gap: 40px;
  }
  .card {
    position: relative; width: 560px; height: 320px;
    border-radius: 18px; overflow: hidden;
    box-shadow: 0 6px 18px rgba(0,0,0,0.18);
  }

  /* Front side */
  .card-front { background: var(--card-white); }
  .front-brand {
    position: absolute; left: 0; top: 0; width: 100%; height: 156px;
    background: linear-gradient(180deg, var(--card-white), var(--card-shade));
    display: flex; align-items: center; justify-content: center;
  }
  .brand-name {
    font-weight: 700; font-size: 58px; letter-spacing: -1px;
    color: var(--brand); line-height: 1;
  }
  .services-band {
    position: absolute; left: 0; top: 156px; width: 100%; height: 24px;
    background: var(--lime);
    display: flex; align-items: center; justify-content: center;
    font-size: 11.5px; color: var(--navy-deep); letter-spacing: 0.1px;
  }
  .services-band .sep { margin: 0 6px; }
  .contact-panel {
    position: absolute; left: 0; top: 180px; width: 100%; height: 140px;
    background: linear-gradient(180deg, var(--navy), var(--navy-deep));
    color: var(--on-navy);
    display: flex; align-items: center;
  }
  .person { width: 290px; padding-left: 46px; }
  .person-name { font-size: 21px; font-weight: 400; margin-bottom: 8px; }
  .person-address { font-size: 13px; font-weight: 300; line-height: 1.45; }
  .divider { width: 1px; height: 72px; background: rgba(255,255,255,0.8); }
  .contact-list { list-style: none; padding-left: 26px; font-size: 13px; font-weight: 300; }
  .contact-list li { display: flex; align-items: center; gap: 9px; line-height: 1.9; }
  .contact-list svg { width: 11px; height: 11px; flex: none; }

  /* Back side */
  .card-back {
    background: radial-gradient(ellipse at 55% 45%, var(--card-white) 40%, #ececec 100%);
  }
  .back-brand {
    position: absolute; left: 0; top: 96px; width: 100%;
    display: flex; justify-content: center;
  }
  .brand-row { display: flex; align-items: center; gap: 14px; }
  .brand-dot { width: 30px; height: 30px; border-radius: 50%; background: var(--brand); }
  .back-brand .brand-name { font-size: 52px; }
  .back-web {
    position: absolute; left: 40px; right: 40px; bottom: 46px;
    display: flex; align-items: center; gap: 16px;
  }
  .back-web .rule-short { width: 22px; height: 1px; background: var(--ink); }
  .back-web .url { font-size: 16px; color: var(--ink); letter-spacing: 0.3px; }
  .back-web .rule-long { flex: 1; height: 1px; background: var(--ink); }
</style>
</head>
<body>
<main class="canvas">

  <section class="card card-front" aria-label="Card front">
    <div class="front-brand">
      <div class="brand-name">ReelBloom</div>
    </div>
    <div class="services-band">
      <span>Training &amp; Enrichment</span><span class="sep">|</span>
      <span>Private &amp; Corporate Entertainment</span><span class="sep">|</span>
      <span>Music composition &amp; production</span>
    </div>
    <div class="contact-panel">
      <div class="person">
        <div class="person-name">Employee Name</div>
        <div class="person-address">Your Address Inc 2nd Lane<br>Ave Millbrook, NJ 00000</div>
      </div>
      <div class="divider"></div>
      <ul class="contact-list">
        <li>
          <svg viewBox="0 0 12 12"><rect x="2.5" y="0.5" width="7" height="11" rx="1.5" fill="none" stroke="#fff" stroke-width="1.2"/><circle cx="6" cy="9.5" r="0.8" fill="#fff"/></svg>
          0098 7654 321
        </li>
        <li>
          <svg viewBox="0 0 12 12"><rect x="0.5" y="2" width="11" height="8" fill="#fff"/><path d="M0.5 2 L6 6.5 L11.5 2" fill="none" stroke="#15266b" stroke-width="1"/></svg>
          info@reelbloom-arts.com
        </li>
        <li>
          <svg viewBox="0 0 12 12"><circle cx="6" cy="6" r="5.3" fill="none" stroke="#fff" stroke-width="1"/><ellipse cx="6" cy="6" rx="2.3" ry="5.3" fill="none" stroke="#fff" stroke-width="0.9"/><line x1="0.7" y1="6" x2="11.3" y2="6" stroke="#fff" stroke-width="0.9"/></svg>
          www.reelbloom-arts.com
        </li>
      </ul>
    </div>
  </section>

  <section class="card card-back" aria-label="Card back">
    <div class="back-brand">
      <div class="brand-row">
        <div class="brand-name">ReelBloom</div>
        <span class="brand-dot"></span>
      </div>
    </div>
    <div class="back-web">
      <span class="rule-short"></span>
      <span class="url">www.reelbloom-arts.com</span>
      <span class="rule-long"></span>
    </div>
  </section>

</main>
</body>
</html>
```